Dynamic Business Card for Sports Supplements Company

Hi! I'm looking for an awesome business card to match my existing sports supplement company. I have uploaded my current company logo and screenshot of the front page of my website.

I would like to have something dynamic and interesting and utilize the colors in the website - the reds and purples

The business card should be double sided and focus on a unique eye-catching design on the back and include all the relevant company info.

Most importantly, it should say somewhere: "Sign up on our website for a coupon code."

Target Market(s)

Mostly for women gym goers but it shouldn't be too feminine. It should be in keeping with the website design. It should flow and clearly be connected to it

Industry/Entity Type

Business

Contact Information for Business Card

Lorraine K. Vestal
CEO
LVestal@Quorvanexco.com
www.quorvanexco.com
555.417.3820
P.O. Box 47315
Lindell, Oregon 00000

Sign up on our website for a coupon code

Font styles to use
Serif
Sans Serif
Other font styles liked:
• Novecento font family and "Quorvanex" is in AR Destine font

Requirements
Must have
• One side should be a bold Quorvanex logo design. Even just the symbol itself may be o.k. (see attached file)

```html
<!DOCTYPE html>
<html lang="en">
<head>
<meta charset="utf-8">
<title>Quorvanex Business Card</title>
<link rel="stylesheet" href="https://fonts.googleapis.com/css2?family=Arimo:wght@400;700&display=swap">
<style>
  :root {
    --stage: #e9e6e1;
    --card-black: #000000;
    --brand-red: #ed1c24;
    --ink-white: #ffffff;
    --tag-grey: #9a9a9a;
    --shadow: rgba(0, 0, 0, 0.28);
  }
  * { box-sizing: border-box; margin: 0; padding: 0; }
  html, body {
    width: 1200px; height: 987px; overflow: hidden;
    background: var(--stage);
    font-family: "Arimo", Arial, sans-serif;
  }
  .stage { position: relative; width: 1200px; height: 987px; }
  .card {
    position: absolute; left: 293px; width: 615px; height: 351px;
    background: var(--card-black); overflow: hidden;
    box-shadow: 0 3px 8px var(--shadow);
  }
  .card--front { top: 130px; }
  .card--back { top: 505px; }

  .brand {
    position: absolute; left: 0; right: 0;
    display: flex; flex-direction: column; align-items: center;
  }
  .brand__lockup { display: flex; align-items: center; gap: 12px; }
  .brand__mark { width: 26px; height: 26px; background: var(--brand-red); }
  .brand__name {
    color: var(--ink-white); font-weight: 700; text-transform: uppercase;
    letter-spacing: 1px; line-height: 1;
  }
  .brand__tagline {
    color: var(--tag-grey); text-transform: uppercase; letter-spacing: 2.2px;
    font-size: 10px; margin-top: 6px;
  }
  .card--front .brand { top: 118px; }
  .card--front .brand__name { font-size: 34px; }
  .card--back .brand { top: 205px; }
  .card--back .brand__name { font-size: 38px; }

  .contact-band { position: absolute; left: 0; top: 0; }
  .person { position: absolute; left: 28px; top: 240px; color: var(--ink-white); }
  .person__name { font-size: 21px; font-weight: 700; }
  .person__role { font-size: 15px; margin-top: 4px; margin-left: 80px; }

  .details {
    position: absolute; right: 28px; top: 220px;
    list-style: none; color: var(--ink-white); font-size: 15px; text-align: right;
  }
  .details li {
    height: 23px; line-height: 23px;
    display: flex; justify-content: flex-end; align-items: center; gap: 6px;
  }
  .details .icon { width: 16px; height: 16px; flex: none; }

  .coupon {
    position: absolute; left: 0; right: 0; top: 291px;
    text-align: center; color: var(--ink-white); font-size: 15px;
  }
</style>
</head>
<body>
<main class="stage">
  <section class="card card--front" aria-label="Card front">
    <div class="brand">
      <div class="brand__lockup">
        <span class="brand__mark"></span>
        <span class="brand__name">Quorvanex</span>
      </div>
      <span class="brand__tagline">Your Training Companion</span>
    </div>

    <svg class="contact-band" width="615" height="351" viewBox="0 0 615 351" aria-hidden="true">
      <path d="M0 210 H77 L88 220 L99 210 H615 V351 H0 Z" fill="var(--brand-red)"/>
      <path d="M0 205 H75 L88 217 L101 205 H615" fill="none" stroke="var(--ink-white)" stroke-width="3"/>
    </svg>

    <div class="person">
      <p class="person__name">Lorraine K. Vestal</p>
      <p class="person__role">CEO</p>
    </div>

    <ul class="details">
      <li>P.O. Box 47315</li>
      <li>Lindell, Oregon 00000</li>
      <li>555.417.3820
        <svg class="icon" viewBox="0 0 16 16" aria-hidden="true"><path d="M2 5 Q8 1 14 5 V7 H11 V5.5 H5 V7 H2 Z M4 8 H12 L13 14 H3 Z" fill="var(--ink-white)"/><circle cx="8" cy="11" r="1.6" fill="var(--brand-red)"/></svg>
      </li>
      <li>LVestal@Quorvanexco.com
        <svg class="icon" viewBox="0 0 16 16" aria-hidden="true"><rect x="1.5" y="3.5" width="13" height="9" fill="var(--ink-white)"/><path d="M1.5 3.5 L8 9 L14.5 3.5" fill="none" stroke="var(--brand-red)" stroke-width="1.2"/></svg>
      </li>
      <li>www.quorvanexco.com
        <svg class="icon" viewBox="0 0 16 16" aria-hidden="true"><circle cx="8" cy="8" r="6.5" fill="var(--ink-white)"/><ellipse cx="8" cy="8" rx="2.6" ry="6.5" fill="none" stroke="var(--brand-red)" stroke-width="1"/><path d="M1.5 8 H14.5" stroke="var(--brand-red)" stroke-width="1"/></svg>
      </li>
    </ul>
  </section>

  <section class="card card--back" aria-label="Card back">
    <div class="brand">
      <div class="brand__lockup">
        <span class="brand__mark"></span>
        <span class="brand__name">Quorvanex</span>
      </div>
      <span class="brand__tagline">Your Training Companion</span>
    </div>
    <p class="coupon">Sign up on our website for a coupon code</p>
  </section>
</main>
</body>
</html>
```